Business Cards for new orthopaedic surgery practice

My husband and I are starting our own orthopaedic surgery practice. We are looking for a business card that is uniform, but one will have my name/title and the other will have his. You can just create one design with my name on it for now. But when I choose your design as the winning design I will ask that you add another copy with his name/title.

We are looking for classy, simple, elite all in one. We like dark blues/a little gold/yellow. Something that goes with our logo. We want our logo incorporated. Here is all the info you need:
Business name: RV Bone & Vitality Center
Location: 38517 North Willowmere Ave
Coral Springs, FL 33071
Phone: 954-218-4063
Fax: 954-582-7341
Email: info@myrvbonecare.example

Names: Lydia Vance, M.D.
Board Certified Hand and Upper Extremity Surgeon

Ebo Dansu, M.D.
Board Certified Hip & Knee Replacement/General Orthopaedic Surgeon

Can decide what you want to put on the back. Maybe a slogan:
Strong in Care. Steady for You

I am just going to upload our logo. The only thing is if we select you as the winning design, the location, and phone numbers may change. We will need your help to update that once fully solidified.

Industry/Entity Type

Medical

Contact Information for Business Card

Colors
0054AA
0677BA
7BADD7
CADEEF
E8F1F8
0094D4
00A9DD
6FCCEA
C7EBF8
E9F6FB

Requirements
Must have
• class, appeal,
Should not have
• We want to air on the side of masculine if we are looking at masculine vs. feminine feel. But we still want it classy, sophisticated, and something we will love

```html
<!DOCTYPE html>
<html lang="en">
<head>
<meta charset="utf-8">
<title>RV Bone &amp; Vitality Center — Business Card</title>
<link href="https://fonts.googleapis.com/css2?family=Montserrat:wght@400;500;700&display=swap" rel="stylesheet">
<style>
  :root {
    --navy: #1b2a4e;
    --navy-deep: #17244a;
    --navy-glow: #34509a;
    --gold: #c9a15a;
    --paper: #ffffff;
    --stage: #c8c8c8;
  }
  * { box-sizing: border-box; margin: 0; padding: 0; }
  html, body { width: 1200px; height: 900px; overflow: hidden; }
  body {
    background: var(--stage);
    font-family: "Montserrat", Arial, sans-serif;
    position: relative;
  }
  .card {
    position: absolute;
    top: 150px;
    width: 343px;
    height: 600px;
    overflow: hidden;
  }
  .card--front { left: 246px; background: var(--paper); color: var(--navy); }
  .card--back { left: 611px; background: var(--navy); color: var(--paper); }

  .brand {
    position: absolute;
    left: 87px;
    width: 168px;
    height: 168px;
    display: flex;
    flex-direction: column;
    align-items: center;
    justify-content: center;
    text-align: center;
    gap: 8px;
    z-index: 1;
  }
  .card--front .brand { top: 46px; }
  .card--back .brand { top: 74px; }
  .brand__mark {
    width: 18px; height: 18px; border-radius: 50%;
    background: currentColor;
  }
  .brand__name {
    font-weight: 700;
    font-size: 17px;
    line-height: 1.25;
    letter-spacing: 0.04em;
    text-transform: uppercase;
  }
  .brand__ring {
    position: absolute; inset: 0;
    width: 168px; height: 168px;
  }

  .person { position: absolute; left: 36px; top: 318px; }
  .person__name {
    color: var(--gold);
    font-weight: 700;
    font-size: 22px;
    letter-spacing: 0.04em;
    line-height: 1;
    white-space: nowrap;
  }
  .person__title { font-size: 13.5px; line-height: 17px; margin-top: 6px; }

  .contact { position: absolute; left: 36px; top: 389px; list-style: none; font-size: 13.5px; line-height: 17px; }
  .contact li { display: flex; align-items: center; gap: 5px; white-space: nowrap; }
  .contact svg { width: 11px; height: 11px; flex: none; }
  .contact .accent { color: var(--gold); }

  .address { position: absolute; left: 36px; top: 481px; font-size: 13.5px; line-height: 17px; font-style: normal; }
  .rule { position: absolute; left: 36px; top: 525px; width: 235px; height: 2px; background: var(--navy); }

  .slogan-band { position: absolute; left: 0; top: 546px; width: 343px; height: 17px; }
  .slogan-band__block { position: absolute; top: 0; height: 17px; }
  .slogan-band__block--navy { left: 0; width: 36px; background: var(--navy); }
  .slogan-band__block--gold { left: 271px; width: 72px; background: var(--gold); }
  .slogan-band__text {
    position: absolute; left: 46px; top: 0; width: 218px;
    font-size: 13.5px; font-weight: 500; line-height: 17px;
    white-space: nowrap;
  }

  .back-emblem {
    position: absolute; left: 0; top: 315px;
    width: 343px; height: 285px;
    background: radial-gradient(ellipse 70% 60% at 45% 30%, rgba(52,80,154,0.85) 0%, rgba(23,36,74,0.6) 60%, rgba(27,42,78,0) 100%);
  }
</style>
</head>
<body>
  <section class="card card--front" aria-label="Business card front">
    <div class="brand">
      <svg class="brand__ring" viewBox="0 0 168 168" aria-hidden="true">
        <circle cx="84" cy="84" r="82" fill="none" stroke="var(--gold)" stroke-width="2"/>
      </svg>
      <span class="brand__mark"></span>
      <span class="brand__name">RV Bone &amp;<br>Vitality<br>Center</span>
    </div>

    <div class="person">
      <h1 class="person__name">LYDIA VANCE, M.D</h1>
      <p class="person__title">Board Certified Hand and<br>Upper Extremity Surgeon</p>
    </div>

    <ul class="contact">
      <li><svg viewBox="0 0 12 12"><path d="M2.5 1l2 2.2-1 1.3c.6 1.4 1.7 2.5 3 3l1.3-1 2.2 2-1.2 1.5C5 10 2 7 1 2.7z" fill="var(--gold)"/></svg><span>954-218-4063</span></li>
      <li><svg viewBox="0 0 12 12" fill="none" stroke="var(--gold)" stroke-width="1"><rect x="3" y="1" width="6" height="3"/><rect x="1" y="4" width="10" height="5"/><rect x="3" y="7" width="6" height="4"/></svg><span>954-582-7341</span></li>
      <li><svg viewBox="0 0 12 12" fill="none" stroke="var(--gold)" stroke-width="1"><rect x="1" y="3" width="10" height="7"/><path d="M1 3l5 4 5-4"/></svg><span>info@myrvbonecare.example</span></li>
      <li><svg viewBox="0 0 12 12" fill="none" stroke="var(--gold)" stroke-width="1"><circle cx="6" cy="6" r="5"/><ellipse cx="6" cy="6" rx="2.2" ry="5"/><path d="M1 6h10M2 3.5h8M2 8.5h8"/></svg><span>www.<span class="accent">myrvbonecare</span>.example</span></li>
    </ul>

    <address class="address">38517 North Willowmere Ave<br>Maple Harbor,FL 34219</address>
    <div class="rule"></div>

    <div class="slogan-band">
      <span class="slogan-band__block slogan-band__block--navy"></span>
      <span class="slogan-band__text">Strong in Care. Steady for You</span>
      <span class="slogan-band__block slogan-band__block--gold"></span>
    </div>
  </section>

  <section class="card card--back" aria-label="Business card back">
    <div class="brand">
      <svg class="brand__ring" viewBox="0 0 168 168" aria-hidden="true">
        <circle cx="84" cy="84" r="82" fill="none" stroke="var(--gold)" stroke-width="2"/>
      </svg>
      <span class="brand__mark"></span>
      <span class="brand__name">RV Bone &amp;<br>Vitality<br>Center</span>
    </div>
    <div class="back-emblem" role="img" aria-label="Large embossed tree and monogram decoration in deep blue tones"></div>
  </section>
</body>
</html>
```